Corvanth Veylor - Advanced Skincare and undetectable Makeup for Men

We are in need of a professional webpage for our company Corvanth Veylor. We help every man feel his best by looking his best. Inspired by the myth of Corvanth, we offer makeup and skincare products along with education upon their use. Our mission is to celebrate masculinity in all of its forms, regardless of age, race, sexual orientation, or assigned gender at birth.

The webpage would serve as our online store, as a place where our clients can learn about our brand, view our "How-to" video tutorials, and get product information. An online blog will also be hosted in order to keep clients up to date with news, updates, media mentions, etc.

The color schemes that we use are mostly Black and Gold, with Red accents. please keep in mind that this is a men's cosmetics line, and therefore should read powerful, sexy, confident and bold - all with a high end look and feel.

Think along the lines of brands like Lem Brisko, QDV, Belluti, etc.

our logo is included in the files attached. images and copy will be added in at a later time; hence, general images that fit the feel and filler text is encouraged.

The products to be sold include:
a face cleanser in a pump dispenser bottle (1 size)
a mask in a round jar container (1 size)
a moisturizer in a pump container 1 size)
a concealer in a click pen with a brush applicator (3 shades)
a liquid liner pen (4 shades)
a contouring palette (2 shade options)
a setting spray (single option)

Target Market(s)

Millennial Men

Industry/Entity Type

Beauty

Number of Pages Required

5+ page

Font styles to use
Serif

Colors
ec1f27
000000
faa54b

Requirements
Must have
• ur essential requirements are:
• 1) a stunning and engaging landing page that truly captures the ideals of sexuality, boldness and confidence.
• 2) an interactive and engaging online store that is easy to update / add product / information to.
• 3) Product pages supporting various toggling images of the product, a shade selection option, ingredient information, usage instructions, pricing, and a link to a "how to video" unique to each individual product.
• 4) dedicated space where all of the tutorials can be organized together
• 5) an organized Blog section, that would include a segment for a Q&A section for us to update as the brand grows, ongoing contests (that would be easily hidden if there are no contests running at the moment) as well as general news and updates segment.
• 6) an "about us" page, where our customers are able to learn about our story, inspirations, humanitarian efforts and philosophies in product contents and purity.
• 7) a contact us page, which would include social media links, contact email and telephone number as well as physical address to be updated upon launch.
• 8) discrete privacy policy, terms of use, and return policy links available at the bottom of every page
Nice to have
• 1) A posting forum where clients could post their looks using our products, or maybe a live stream of our Pictoval account.
• 2) a member sign in page so that we can collect and store customer information for faster check out, keep track of purchases attached to their email address (future loyalty program plans) and maintain an email database for email notifications and the such.

```html
<!DOCTYPE html>
<html lang="en">
<head>
<meta charset="utf-8">
<title>Liquid Liner – Corvanth Veylor</title>
<link href="https://fonts.googleapis.com/css2?family=Montserrat:wght@400;500;600;700&family=Cinzel:wght@500&display=swap" rel="stylesheet">
<style>
:root{
  --page:#d9d9d7;
  --ink:#3a3a3a;
  --ink-soft:#555;
  --black:#000;
  --white:#fff;
  --gold:#b28439;
  --gold-band:#a57c3c;
  --chip:#3d3d3d;
  --footer-text:#9a9a9a;
  --footer-rule:#2a2a2a;
  --field-line:#cfcfcf;
}
*{box-sizing:border-box;margin:0;padding:0}
html,body{width:1200px;height:1101px;overflow:hidden}
body{font-family:"Montserrat",sans-serif;background:var(--page);color:var(--ink);position:relative}
a{color:inherit;text-decoration:none}
.abs{position:absolute}

/* header */
.brand{left:86px;top:22px;width:80px;text-align:center}
.brand-square{width:22px;height:22px;border:2px solid var(--gold);margin:0 auto 7px}
.brand-name{font-family:"Cinzel",serif;font-size:6px;letter-spacing:.8px;color:var(--gold);white-space:nowrap}
.main-nav{left:180px;top:37px;font-size:10px;font-weight:500;color:#555;letter-spacing:.3px}
.main-nav a{position:absolute;white-space:nowrap}
.cart{left:763px;top:37px;font-size:10px;color:#444;display:flex;align-items:center;gap:5px;white-space:nowrap}
.account{left:836px;top:25px;width:33px;height:33px;border-radius:50%;border:1px solid #b5b5b5;background:#e4e4e2;box-shadow:0 2px 4px rgba(0,0,0,.15);display:flex;align-items:center;justify-content:center}
.search{left:886px;top:27px;width:190px;height:32px;background:var(--black);border-radius:4px;display:flex;align-items:center;padding-left:10px;gap:8px;color:var(--white);font-size:10px}
.langs{left:1110px;top:40px;display:flex;gap:6px}
.langs span{width:10px;height:7px;display:block}

/* product */
.product-photo{left:264px;top:142px;width:278px;height:315px;border-radius:8px;background:radial-gradient(circle at 50% 55%,#f1f1ef 0%,#dfdfdd 75%);box-shadow:0 6px 16px rgba(0,0,0,.12)}
.product-photo .item{position:absolute;left:85px;top:55px;width:110px;height:200px;border-radius:6px;background:linear-gradient(90deg,#8fc43a,#b7df5d 50%,#79b02b)}
.thumb{top:490px;width:79px;height:82px;border:1px solid #444;background:#dcdcda}
.thumb i{position:absolute;left:18px;top:12px;width:42px;height:56px;border-radius:3px;background:linear-gradient(90deg,#8fc43a,#b9df60)}
.thumb.jar i{left:14px;top:26px;width:50px;height:32px;border-radius:8px;background:linear-gradient(#ececec,#bdbdbd)}

.back-link{left:577px;top:133px;font-size:9px;color:#666;letter-spacing:.5px}
.product-title{left:577px;top:162px;font-size:27px;font-weight:500;color:#444;letter-spacing:.3px}
.price{left:577px;top:197px;height:27px;width:69px;background:var(--chip);color:var(--white);font-size:12px;font-weight:600;display:flex;align-items:center;justify-content:space-around}
.price b{width:1px;height:27px;background:#666}
.description{left:577px;top:236px;width:372px;font-size:10.4px;line-height:16.4px;color:#333}
.colour{left:577px;top:364px;display:flex;align-items:center;font-size:8px;letter-spacing:.6px;color:#444}
.swatch{width:13px;height:13px;border-radius:50%;margin-left:12px}
.included{left:577px;top:387px;width:368px}
.included h4{font-size:6.5px;font-weight:600;letter-spacing:.6px;color:#444;padding-bottom:4px;border-bottom:1px solid #bcbcbc}
.included ul{list-style:none;margin-top:4px;padding-left:18px}
.included li{font-size:6.5px;color:#444;line-height:12.3px;letter-spacing:.3px}
.included li::before{content:"•";margin-right:4px}
.add-to-cart{left:577px;top:481px;width:89px;height:27px;background:var(--chip);color:var(--white);font-size:9px;font-weight:600;letter-spacing:1.3px;border-radius:3px;display:flex;align-items:center;justify-content:center;box-shadow:0 2px 4px rgba(0,0,0,.25)}

/* footer */
.site-footer{left:0;top:628px;width:1200px;height:473px;background:var(--black);color:var(--footer-text)}
.footer-brand{left:244px;top:84px;width:102px;text-align:center}
.footer-about{left:248px;top:145px;width:222px;font-size:10.5px;line-height:17px;color:#a8a8a8}
.footer-col{top:73px;font-size:10.5px}
.footer-col h5{font-weight:500;font-size:10.5px;color:#a8a8a8;margin-bottom:9px}
.footer-col a{display:block;margin-left:9px;line-height:22.8px;color:#a8a8a8}
.friends{left:0;width:1200px;top:294px;text-align:center;color:var(--white);font-size:15px}
.social{top:326px;width:32px;height:32px;border-radius:50%;border:1px solid #777}
.footer-rule{left:240px;top:375px;width:720px;height:1px;background:var(--footer-rule)}
.legal{top:406px;font-size:8px;color:#bbb}
.copyright{left:680px;width:250px;text-align:right;top:406px;font-size:8px;color:#bbb}

/* contact widget */
.contact-widget{left:957px;top:577px;width:221px;height:339px;background:var(--white);box-shadow:0 3px 12px rgba(0,0,0,.3)}
.widget-head{height:31px;background:var(--gold-band);display:flex;align-items:center;padding-left:10px;gap:12px;color:var(--white);font-size:9px;font-weight:600}
.widget-head .toggle{margin-left:auto;width:26px;height:31px;background:#8c6a31;display:flex;align-items:center;justify-content:center}
.widget-body{padding:14px 10px 0}
.widget-body h6{font-size:10.5px;font-weight:600;color:#333}
.widget-body p{font-size:10px;font-weight:500;color:#444;margin-top:10px}
.field{height:31px;border:1px solid var(--field-line);margin-top:5px;display:flex;align-items:center;font-size:9px;color:#777}
.field:first-of-type{margin-top:13px}
.field .ico{width:30px;height:100%;border-right:1px solid var(--field-line);display:flex;align-items:center;justify-content:center;margin-right:10px}
.message{height:79px;border:1px solid var(--field-line);margin-top:5px;font-size:9px;color:#777;padding:7px}
.send{height:31px;background:var(--black);color:var(--white);font-size:9.5px;font-weight:600;display:flex;align-items:center;justify-content:center;margin-top:6px}
</style>
</head>
<body>

<header>
  <a class="brand abs" href="#"><div class="brand-square"></div><div class="brand-name">CORVANTH VEYLOR</div></a>
  <nav class="main-nav abs">
    <a href="#" style="left:0">HOME</a>
    <a href="#" style="left:53px">PRODUCTS &nbsp;›</a>
    <a href="#" style="left:140px">ABOUT US</a>
    <a href="#" style="left:212px">CONTACT</a>
    <a href="#" style="left:280px">BLOG</a>
  </nav>
  <a class="cart abs" href="#">
    <svg width="13" height="11" viewBox="0 0 13 11" fill="none" stroke="#444" stroke-width="1.1"><path d="M0 1h2l2 6h7l1.5-4.5H3"/><circle cx="5" cy="9.5" r="1"/><circle cx="10" cy="9.5" r="1"/></svg>
    CART (0)
  </a>
  <a class="account abs" href="#" aria-label="Account">
    <svg width="14" height="14" viewBox="0 0 14 14" fill="none" stroke="#444" stroke-width="1.1"><circle cx="7" cy="4.5" r="3"/><path d="M1.5 13.5c0-3 2.5-5 5.5-5s5.5 2 5.5 5"/></svg>
  </a>
  <div class="search abs">
    <svg width="11" height="11" viewBox="0 0 11 11" fill="none" stroke="#fff" stroke-width="1.2"><circle cx="4.5" cy="4.5" r="3.5"/><path d="M7 7l3.5 3.5"/></svg>
    Search Corvanth Veylor
  </div>
  <div class="langs abs">
    <span style="background:linear-gradient(90deg,#2c4aa0 33%,#eee 33% 66%,#d33 66%)"></span>
    <span style="background:linear-gradient(90deg,#2a9a4a 33%,#eee 33% 66%,#d33 66%)"></span>
    <span style="background:linear-gradient(#c33 33%,#eee 33% 66%,#2c4aa0 66%)"></span>
  </div>
</header>

<main>
  <div class="product-photo abs" role="img" aria-label="Product photo: green liquid liner bottle beside its box"><div class="item"></div></div>
  <div class="thumb abs" style="left:270px" role="img" aria-label="Thumbnail: tube with box"><i></i></div>
  <div class="thumb abs" style="left:365px" role="img" aria-label="Thumbnail: bottle with box"><i></i></div>
  <div class="thumb jar abs" style="left:457px" role="img" aria-label="Thumbnail: open cream jar"><i></i></div>

  <a class="back-link abs" href="#">‹ BACK TO LIQUID LINER</a>
  <h1 class="product-title abs">Liquid Liner</h1>
  <div class="price abs"><span>$</span><b></b><span>299.98</span></div>
  <p class="description abs">Pellentesque congue ultrices elit sed sodales. Donec volutpat metus eu dolor finibus ornare. Donec venenatis porta mauris eget congue. Aenean vel enim pulvinar, egestas dui ut, egestas nisi. Vivamus vitae enim venenatis, elementum augue et, fermentum ligula. Cras vulputate, sapien sit amet ullamcorper suscipit, ex lacus fermentum libero, sed pellentesque tortor sapien vel leo. Donec consequat libero ac orci porta pellentesque.</p>
  <div class="colour abs">COLOUR
    <span class="swatch" style="background:#19b6f0;margin-left:18px"></span>
    <span class="swatch" style="background:#e21414"></span>
    <span class="swatch" style="background:#1b10e8"></span>
  </div>
  <div class="included abs">
    <h4>WHATS INCLUDED</h4>
    <ul>
      <li>5 STANDARD CHIP BRUSHES (SIZES 2 1/2", 4")</li>
      <li>2 GOLDEN SYNTHETIC SHADER BRUSHES (SIZES 6, 8)</li>
      <li>2 WHITE SYNTHETIC SHADER BRUSHES (SIZES 6, 8)</li>
      <li>1 WHITE SYNTHETIC LINER BRUSH (SIZE 1)</li>
    </ul>
  </div>
  <a class="add-to-cart abs" href="#">ADD TO CART</a>
</main>

<footer class="site-footer abs">
  <div class="footer-brand abs"><div class="brand-square" style="width:26px;height:26px;margin-bottom:9px"></div><div class="brand-name" style="font-size:7px">CORVANTH VEYLOR</div></div>
  <p class="footer-about abs">Lorem ipsum dolor sit amet, consectetur adipiscing elit. Suspendisse varius enim in eros elementum tristique. Duis cursus, mi quis viverra ornare, eros dolor interdum nulla, ut commodo diam libero vitae erat. Aenean faucibus nibh et justo cursus id rutrum lorem imperdiet. Nunc ut sem vitae risus tristique posuere.</p>
  <div class="footer-col abs" style="left:486px">
    <h5>Resources</h5>
    <a href="#">Licenses</a><a href="#">Blog</a><a href="#">Discussions</a><a href="#">Products</a><a href="#">Collections</a><a href="#">Help Center</a>
  </div>
  <div class="footer-col abs" style="left:726px">
    <h5>Company</h5>
    <a href="#">About</a><a href="#">Brand</a><a href="#">Terms</a><a href="#">Cookie Policy</a><a href="#">Privacy Policy</a><a href="#">Careers</a>
  </div>
  <p class="friends abs">let's be friends</p>
  <a class="social abs" href="#" style="left:504px" aria-label="Social profile one"></a>
  <a class="social abs" href="#" style="left:584px" aria-label="Social profile two"></a>
  <a class="social abs" href="#" style="left:664px" aria-label="Pictoval"></a>
  <div class="footer-rule abs"></div>
  <a class="legal abs" href="#" style="left:258px">Privacy Policy</a>
  <a class="legal abs" href="#" style="left:336px">Terms Of Use</a>
  <a class="legal abs" href="#" style="left:411px">Return Policy</a>
  <p class="copyright abs">© Copyright 2018 Corvanth Veylor. All Rights Reserved.</p>
</footer>

<aside class="contact-widget abs">
  <div class="widget-head">
    <svg width="14" height="12" viewBox="0 0 14 12" fill="none" stroke="#fff" stroke-width="1"><rect x="0.5" y="0.5" width="9" height="6"/><path d="M4 8.5v1h6l2.5 2v-2h1V3.5h-3"/></svg>
    Contact Us
    <span class="toggle"><svg width="9" height="6" viewBox="0 0 9 6" fill="none" stroke="#fff" stroke-width="1.3"><path d="M1 5l3.5-3.5L8 5"/></svg></span>
  </div>
  <div class="widget-body">
    <h6>How Can We Help You?</h6>
    <p>Please, leave us your message.</p>
    <div class="field"><span class="ico"><svg width="12" height="12" viewBox="0 0 12 12" fill="none" stroke="#333" stroke-width="1.1"><circle cx="6" cy="3.5" r="2.5"/><path d="M1 11.5c0-2.8 2.2-4.5 5-4.5s5 1.7 5 4.5"/></svg></span>Enter your name</div>
    <div class="field"><span class="ico"><svg width="13" height="10" viewBox="0 0 13 10" fill="none" stroke="#333" stroke-width="1.1"><rect x="0.5" y="0.5" width="12" height="9"/><path d="M0.5 0.5l6 5 6-5"/></svg></span>Enter your email</div>
    <div class="field"><span class="ico"><svg width="12" height="12" viewBox="0 0 12 12" fill="none" stroke="#333" stroke-width="1.1"><path d="M1 2.5c0 5 3.5 8.5 8.5 8.5l1.5-2-2.5-1.5-1.3 1.1C5.6 8 4 6.4 3.4 4.8L4.5 3.5 3 1z"/></svg></span>Enter your phone</div>
    <div class="message">How can we help you?</div>
    <div class="send">Send Message</div>
  </div>
</aside>

</body>
</html>
```